Business Card for a Dental Office

The design should communicate integrity, quality and reliability. We also want the card look elegant, simple, but still stand out, different from the traditional-dental-office business card.

Industry/Entity Type

Business

```html
<!DOCTYPE html>
<html lang="en">
<head>
<meta charset="utf-8">
<title>Harlow Dental Studio – Business Card</title>
<link rel="stylesheet" href="https://fonts.googleapis.com/css2?family=Arimo:wght@400;700&display=swap">
<style>
  :root {
    --stage: #2b2b2d;
    --card: #ffffff;
    --ink: #0d0d0d;
    --gold: #d4b41c;
    --text: #555555;
    --muted: #666666;
    --white: #ffffff;
  }
  * { box-sizing: border-box; margin: 0; padding: 0; }
  html, body { width: 1200px; height: 950px; overflow: hidden; }
  body {
    background: var(--stage);
    font-family: "Arimo", Arial, sans-serif;
    position: relative;
  }
  .card {
    position: absolute;
    width: 620px;
    height: 354px;
    background: var(--card);
    overflow: hidden;
    box-shadow: 0 10px 30px rgba(0,0,0,.45);
  }

  /* Front */
  .card-front { left: 110px; top: 80px; }
  .brand-mark {
    position: absolute;
    left: 0; right: 0; top: 120px;
    display: flex; align-items: center; justify-content: center; gap: 14px;
  }
  .brand-square { width: 46px; height: 46px; background: var(--gold); flex: none; }
  .brand-name { font-size: 30px; font-weight: 700; color: var(--ink); letter-spacing: .5px; }
  .front-web {
    position: absolute; left: 0; right: 0; top: 240px;
    text-align: center; font-size: 15px; letter-spacing: 4px; color: var(--muted);
  }

  /* Back */
  .card-back { left: 470px; top: 510px; }
  .back-art { position: absolute; inset: 0; width: 620px; height: 354px; }
  .person { position: absolute; right: 40px; top: 18px; }
  .person-name { color: var(--gold); font-size: 22px; font-weight: 700; line-height: 26px; }
  .person-role { color: var(--white); font-size: 15px; line-height: 18px; margin-top: 2px; margin-left: 20px; }

  .contact {
    position: absolute; left: 375px; top: 160px;
    list-style: none; color: var(--text); font-size: 14.5px; line-height: 19px;
  }
  .contact li { display: flex; align-items: center; gap: 8px; white-space: nowrap; }
  .contact svg { width: 13px; height: 13px; flex: none; fill: #222; }

  .back-brand {
    position: absolute; left: 30px; top: 290px;
    display: flex; align-items: center; gap: 10px;
  }
  .back-brand .brand-square { width: 30px; height: 30px; }
  .back-brand .brand-name { font-size: 20px; }
</style>
</head>
<body>

<section class="card card-front" aria-label="Card front">
  <div class="brand-mark">
    <span class="brand-square"></span>
    <span class="brand-name">Harlow Dental Studio</span>
  </div>
  <p class="front-web">www.harlowdental.com</p>
</section>

<section class="card card-back" aria-label="Card back">
  <svg class="back-art" viewBox="0 0 620 354" aria-hidden="true">
    <path class="band-dark" d="M0,0 H620 V100 C540,110 470,135 400,140 C270,150 120,160 0,230 Z" fill="var(--ink)"/>
    <path class="band-gold" d="M400,140 C270,150 120,160 0,230 L0,262 C100,192 250,158 400,140 Z" fill="var(--gold)"/>
    <path class="band-light" d="M620,80 C560,86 500,110 420,126" fill="none" stroke="var(--white)" stroke-width="5" stroke-linecap="round"/>
  </svg>

  <div class="person">
    <p class="person-name">Marcus Hale</p>
    <p class="person-role">President</p>
  </div>

  <ul class="contact">
    <li>2170 Alder Crest Road</li>
    <li>Maple Ridge, NY 11020</li>
    <li><svg viewBox="0 0 16 16"><path d="M3 2h3l1 4-2 1c1 2 2 3 4 4l1-2 4 1v3c0 1-1 1-2 1C7 14 2 9 2 4c0-1 0-2 1-2z"/></svg>555 0142 2210</li>
    <li><svg viewBox="0 0 16 16"><path d="M4 1h8v14H4zM5.5 3v9h5V3z"/></svg>555 0187 4436</li>
    <li><svg viewBox="0 0 16 16"><path d="M4 1h8v4h2v8H2V5h2zM5 2v3h6V2zM4 9v5h8V9z"/></svg>555 0163 9081</li>
    <li><svg viewBox="0 0 16 16"><path d="M1 3h14v10H1zM2 4l6 5 6-5z"/></svg>marcus@harlowdental.com</li>
    <li><svg viewBox="0 0 16 16"><circle cx="8" cy="8" r="7"/></svg>www.harlowdental.com</li>
  </ul>

  <div class="back-brand">
    <span class="brand-square"></span>
    <span class="brand-name">Harlow Dental Studio</span>
  </div>
</section>

</body>
</html>
```